Business Card Design

I am an Event and Wedding Planner in need of an eye catching business card featuring my logo (attached), my contact details, and my company tagline (Making every celebration glow with wonder...) I would like the tagline in font similar the logo's font.
Updates
I have just noticed that my logo has a misspelling so for the final design, I will be uploading a corrected logo as soon as I have it.
My apologies.
Reason: Waiting on a corrected logo...Lantern is misspelled and it should say Weddings not Wedding
The logo has been corrected so now Lantern is spelled correctly and it says Weddings instead of Wedding. Please use Edwardian Script ITC as the font for the tagline so it will match the logo. Thank you for your patience.
Target Market(s)
Engaged couples and people hosting milestone celebrations. 25-50 years old, predominately female
Industry/Entity Type
Business
Contact Information for Business Card
Rosalind Merrow, Event Manager / Owner, Mobile: 0491 868 254, Email: rosalind@velvetlanternco.com.au, www.velvetlanternco.com.au, Making every celebration glow with wonder...

```html
<!DOCTYPE html>
<html lang="en">
<head>
<meta charset="utf-8">
<title>Velvet Lantern – Business Card</title>
<link rel="stylesheet" href="https://fonts.googleapis.com/css2?family=Carlito:wght@400&family=Pinyon+Script&display=swap">
<style>
  :root {
    --backdrop: #dfe5e8;
    --card-white: #ffffff;
    --card-dark: #2f2b2c;
    --card-dark-deep: #1f1c1d;
    --ink: #2a2a2a;
    --ink-soft: #555555;
    --accent-red: #d6392f;
    --text-light: #f4f4f4;
    --rule: #8a8a8a;
  }
  * { box-sizing: border-box; margin: 0; padding: 0; }
  html, body {
    width: 1200px; height: 960px; overflow: hidden;
    background: var(--backdrop);
  }
  .canvas {
    position: relative; width: 1200px; height: 960px;
    display: flex; flex-direction: column; align-items: center; justify-content: center; gap: 40px;
  }
  .card {
    position: relative; width: 700px; height: 400px;
    box-shadow: 0 8px 24px rgba(0,0,0,0.18);
    overflow: hidden;
  }
  /* Front */
  .card--front { background: var(--card-white); }
  .brand-block {
    position: absolute; left: 0; top: 70px; width: 330px;
    display: flex; flex-direction: column; align-items: center;
  }
  .brand-name {
    display: flex; align-items: center; gap: 12px;
    font-family: "Carlito", sans-serif; font-weight: 400;
    font-size: 40px; color: var(--ink); letter-spacing: 0.5px;
  }
  .brand-dot {
    width: 14px; height: 14px; border-radius: 50%;
    background: var(--accent-red); flex: none;
  }
  .brand-rule {
    width: 240px; height: 1px; background: var(--rule); margin-top: 14px;
  }
  .tagline {
    position: absolute; left: 0; top: 245px; width: 330px;
    text-align: center;
    font-family: "Pinyon Script", cursive;
    font-size: 30px; line-height: 1.25; color: var(--ink-soft);
  }
  .contact-panel {
    position: absolute; left: 330px; top: 22px; width: 345px; height: 356px;
    background: linear-gradient(160deg, var(--card-dark) 0%, var(--card-dark-deep) 100%);
    font-family: "Carlito", sans-serif; color: var(--text-light);
  }
  .person {
    position: absolute; right: 22px; top: 22px; text-align: right;
  }
  .person-name { font-size: 30px; line-height: 1.1; }
  .person-role { font-size: 17px; color: var(--accent-red); margin-top: 8px; }
  .contact-list {
    position: absolute; left: 16px; bottom: 30px; list-style: none;
    font-size: 17px; line-height: 1.75;
  }
  .contact-label { color: var(--accent-red); }
  /* Back */
  .card--back {
    background: linear-gradient(160deg, var(--card-dark) 0%, var(--card-dark-deep) 100%);
    display: flex; flex-direction: column; align-items: center; justify-content: center;
  }
  .card--back .brand-name { color: var(--text-light); font-size: 58px; gap: 16px; }
  .card--back .brand-dot { width: 18px; height: 18px; }
  .card--back .brand-rule { width: 380px; background: #6d6869; margin-top: 22px; }
</style>
</head>
<body>
<main class="canvas">
  <section class="card card--front" aria-label="Business card front">
    <div class="brand-block">
      <div class="brand-name"><span>Velvet Lantern</span><span class="brand-dot"></span></div>
      <div class="brand-rule"></div>
    </div>
    <p class="tagline">Making every celebration<br>glow with wonder...</p>
    <div class="contact-panel">
      <div class="person">
        <p class="person-name">Rosalind Merrow</p>
        <p class="person-role">Event Manager / Owner</p>
      </div>
      <ul class="contact-list">
        <li><span class="contact-label">Ph:</span> 0491 868 254</li>
        <li><span class="contact-label">Mail:</span> rosalind@velvetlanternco.com.au</li>
        <li><span class="contact-label">Web:</span> www.velvetlanternco.com.au</li>
      </ul>
    </div>
  </section>

  <section class="card card--back" aria-label="Business card back">
    <div class="brand-name"><span>Velvet Lantern</span><span class="brand-dot"></span></div>
    <div class="brand-rule"></div>
  </section>
</main>
</body>
</html>
```